Home Page Design (+50 More Pages To Winning Designer!)

We have a 50+ page website, but we're starting with the home page. The winning designer will get all 50+ pages to design as a 2nd project, so make sure you do your best!

Velorane is in the private jet industry and needs a re-designed website.

We have created the structure for the website and content inside of Frandle.io (THESE ARE ONLY ROUGH A.I. GENERATED WIREFRAMES AND DO NOT NEED TO BE FOLLOWED EXACTLY) - https://www.frandle.io/app/project/K482915_qWmRtZaLs-KDnHoUvvy82QJ5cfhaR61trkwqlDV3Hm

Take the content from the 'Home Page' under the 'Wireframe' tab on the Frandle.io link above, but feel free to re-design the page in a better way as these are only A.I. generated wireframes.

We want a DARK theme.... High quality, luxurious feel, greyscale colors. Attached is a brand guideline (BUT THIS IS NOT A 100% BRAND GUIDELINE, YOU CAN CHANGE COLORS AND FONTS AND MAKE CHANGES IF YOU HAVE BETTER IDEAS) and attached is our logo. We are also attaching some examples of other apps and websites to give you a guideline of what we're looking for for this design project.

The final design MUST communicate luxury using high-quality imagery of large cabin luxurious private jets.
Updates

ENTRIES THAT DO NOT FOLLOW THE PROJECT BRIEF WILL BE AUTOMATICALLY DISCARDED. FOLLOW THE INSTRUCTIONS!

Industry/Entity Type

Travel

Number of Pages Required

1 page

Font styles to use
Sans Serif

Colors

Designer to choose colors to be used in the design.

Requirements
Must have
• Follow wireframe and use content in wireframe (see Frandle.io link)

```html
<!DOCTYPE html>
<html lang="en">
<head>
<meta charset="utf-8">
<title>Velorane — Luxury in the Skies</title>
<link href="https://fonts.googleapis.com/css2?family=Bebas+Neue&family=Montserrat:ital,wght@0,400;0,500;0,600;0,700;1,400;1,500&family=Syncopate:wght@400;700&family=Archivo+Black&display=swap" rel="stylesheet">
<style>
:root{
  --black:#000;
  --ink:#0b0b0b;
  --white:#fff;
  --gold:#c9a816;
  --card:#5b5b5b;
  --card-foot:#3a3a3a;
  --muted:#bdbdbd;
  --bar:#5e5e5e;
}
*{margin:0;padding:0;box-sizing:border-box}
html,body{width:1200px;height:3438px;overflow:hidden;background:var(--black)}
body{font-family:"Montserrat",sans-serif;color:var(--white)}
.page{position:relative;width:1200px;height:3438px;overflow:hidden;background:var(--black)}
.abs{position:absolute}
a{color:inherit;text-decoration:none}

/* nav */
.site-nav{left:0;top:0;width:1200px;height:56px;background:var(--white);color:#111}
.brand{display:flex;align-items:center;gap:6px;font-family:"Montserrat",sans-serif;font-weight:500;font-size:20px;letter-spacing:-.3px}
.brand-mark{width:12px;height:12px;background:currentColor}
.site-nav .brand{position:absolute;left:212px;top:17px}
.nav-links{position:absolute;left:350px;top:23px;display:flex;gap:0;font-size:8.5px;font-weight:500;letter-spacing:.3px}
.nav-links span{margin-right:27px}

/* buttons */
.btn{display:flex;align-items:center;justify-content:center;background:var(--gold);color:var(--white);font-family:"Syncopate",sans-serif;font-weight:700;font-size:7.5px;letter-spacing:1.4px}
.btn-outline{background:transparent;border:2px solid var(--white)}
.btn-white{background:var(--white);color:#111}

/* hero */
.hero-photo{left:0;top:56px;width:1200px;height:474px;
  background:radial-gradient(ellipse 420px 300px at 760px 220px,#8a6a3a 0%,#3a2d1e 45%,transparent 75%),
  radial-gradient(ellipse 700px 200px at 300px 480px,#2b2418 0%,transparent 70%),
  linear-gradient(180deg,#0e0f12 0%,#17171a 60%,#1d1a15 100%)}
.hero-title{left:214px;top:276px;font-family:"Bebas Neue",sans-serif;font-size:52px;letter-spacing:3px;line-height:1}
.hero-copy{left:214px;top:327px;width:470px;font-size:13px;line-height:20px}
.hero-btn-tour{left:214px;top:429px;width:126px;height:30px}
.hero-btn-quote{left:362px;top:429px;width:124px;height:30px}

/* fractional */
.frac-title{left:0;top:550px;width:1200px;text-align:center;font-family:"Archivo Black",sans-serif;font-size:22px;letter-spacing:.6px}
.frac-sub{left:0;top:582px;width:1200px;text-align:center;font-size:12.5px;font-weight:600}
.frac-btn{left:527px;top:622px;width:154px;height:32px}
.scroll-cue{left:585px;top:683px;width:40px;height:40px;border-radius:50%;background:var(--white);display:flex;align-items:center;justify-content:center}
.benefit{top:761px;width:172px;height:160px;background:var(--card);clip-path:polygon(0 0,100% 0,100% 92%,95% 100%,0 100%)}
.benefit svg{position:absolute;left:12px;top:13px}
.benefit p{position:absolute;left:12px;top:56px;width:150px;font-size:7.5px;font-weight:600;line-height:14px}
.benefit .label{position:absolute;left:0;bottom:0;width:100%;height:27px;background:var(--card-foot);display:flex;align-items:center;justify-content:center;font-family:"Syncopate",sans-serif;font-weight:700;font-size:8px;letter-spacing:1px}

/* redefining */
.redef-title{left:214px;top:999px;font-family:"Archivo Black",sans-serif;font-size:21px;letter-spacing:.4px}
.redef-tags{left:214px;top:1039px;font-size:11px;word-spacing:1px}
.redef-copy{left:213px;top:1066px;width:460px;font-size:9.8px;line-height:21.4px}
.redef-btn{left:213px;top:1206px;width:154px;height:33px}
.redef-photo{left:705px;top:953px;width:493px;height:334px;background:linear-gradient(120deg,#e2e2e2 0%,#8f8f8f 35%,#3a3a3a 65%,#141414 100%)}

/* elevate */
.elevate-photo{left:0;top:1319px;width:1200px;height:530px;background:linear-gradient(180deg,#061a33 0%,#0a2a55 35%,#1f5a96 62%,#7aa7cf 78%,#4e7aa6 90%,#2b4d75 100%)}
.elevate-title{left:214px;top:1352px;font-family:"Archivo Black",sans-serif;font-size:22px;letter-spacing:1.2px}
.elevate-tags{left:214px;top:1388px;font-size:14px;font-weight:500}
.elevate-copy{left:214px;top:1420px;width:570px;font-size:12px;line-height:23.5px}
.service{top:1638px;width:110px;text-align:center;font-family:"Syncopate",sans-serif;font-weight:700;font-size:8px;letter-spacing:1.2px;line-height:11px;color:#eef3f8}
.service svg{display:block;margin:0 auto 6px}
.elevate-cta{left:0;top:1712px;width:1200px;text-align:center;font-size:11.5px;font-weight:700;color:#0c0c0c}
.elevate-btn{left:522px;top:1757px;width:155px;height:32px}

/* testimonials */
.testi-bg{left:0;top:1849px;width:1200px;height:514px;background:radial-gradient(ellipse 600px 260px at 600px 250px,#2a2a2a 0%,#161616 60%,#0e0e0e 100%)}
.testi-title{left:214px;top:1886px;width:520px;font-family:"Archivo Black",sans-serif;font-size:16.5px;line-height:25px;letter-spacing:.3px}
.testi-btn{left:214px;top:1985px;width:165px;height:35px}
.bubble{position:absolute}
.bubble p{position:absolute;font-size:9.5px;font-style:italic;font-weight:500;line-height:15px;color:#1a1a1a}
.quote-mark{position:absolute;width:48px;height:48px;border-radius:50%;background:var(--black);border:3px solid var(--white);display:flex;align-items:center;justify-content:center;font-family:"Archivo Black",sans-serif;font-size:42px;line-height:1;padding-top:18px;color:var(--white)}

/* partners */
.partner{top:2430px;font-family:"Montserrat",sans-serif;font-weight:600;font-size:17px;letter-spacing:2.5px}
.newsletter-text{left:0;top:2476px;width:1200px;text-align:center;font-size:10.5px;letter-spacing:.6px;line-height:16.5px;color:#d0d0d0}
.email-field{left:491px;top:2530px;width:219px;height:16px;border-bottom:2px solid var(--white);text-align:center;font-size:10.5px;font-style:italic;color:#cfcfcf}
.subscribe-btn{left:539px;top:2557px;width:123px;height:31px}

/* faq */
.faq-photo{left:0;top:2639px;width:518px;height:347px;background:radial-gradient(ellipse 220px 90px at 250px 200px,#e9e2e2 0%,#8a3a40 50%,transparent 80%),linear-gradient(180deg,#1c1c20 0%,#2a2528 60%,#4a1a1f 100%)}
.faq-title{left:554px;top:2638px;font-size:22px;font-weight:500;letter-spacing:.3px}
.faq-item{left:554px;width:410px;font-size:13px;line-height:21px}
.faq-rule{left:554px;width:410px;height:1px;background:#d8d8d8}
.faq-answer{left:552px;top:2906px;width:414px;font-size:8.8px;font-style:italic;line-height:16px;color:#cfcfcf}

/* footer */
.footer-brand{left:214px;top:3010px;color:var(--white)}
.footer-tag{left:214px;top:3042px;width:340px;font-size:9.8px;line-height:16px}
.social{top:3083px;width:13px;height:13px;border-radius:50%;background:var(--white)}
.footer-links{left:214px;top:3122px;width:750px;display:flex;justify-content:space-between;font-size:10px;font-weight:600}
.footer-rule{left:214px;top:3144px;width:750px;height:2px;background:#cfcfcf}
.contact-title{left:214px;top:3178px;font-size:18px;font-weight:500}
.contact-row{left:214px;display:flex;gap:11px;font-size:11px;line-height:18px}
.contact-row svg{flex:none;margin-top:3px}
.footer-cta{left:709px;top:3193px;width:270px;font-size:12px;line-height:19.5px}
.footer-btn{left:709px;top:3287px;width:124px;height:34px}
.legal-bar{left:0;top:3380px;width:1200px;height:58px;background:var(--bar);font-size:11px}
.legal-bar span{position:absolute;top:22px}
</style>
</head>
<body>
<div class="page">

  <!-- Navigation -->
  <header class="abs site-nav">
    <div class="brand"><span>Velorane</span><span class="brand-mark"></span></div>
    <nav class="nav-links">
      <span>AIRCRAFT</span><span>PROGRAMS</span><span>WHY VELORANE</span><span>LIFESTYLE</span><span>SUSTAINABILITY</span><span>RESOURCES</span><span>COMPETITORS</span><span>INQUIRE</span>
    </nav>
  </header>

  <!-- Hero -->
  <div class="abs hero-photo" role="img" aria-label="Large private jet flying low over a city lit up at night"></div>
  <h1 class="abs hero-title">LUXURY IN THE SKIES</h1>
  <p class="abs hero-copy">Soaring above expectations, Velorane invites you to experience luxury in the skies. Unlock the epitome of luxury with Velorane's fleet of exclusive aircraft.Elevate your journey with Velorane and indulge in unparalleled luxury aloft.</p>
  <a class="abs btn hero-btn-tour">BEGIN YOUR TOUR</a>
  <a class="abs btn btn-outline hero-btn-quote">GET A QUOTE</a>

  <!-- Fractional ownership -->
  <h2 class="abs frac-title">Luxury of Private Jet Travel with Fractional Ownership</h2>
  <p class="abs frac-sub">Enjoy Hassle-Free Access and Flexibility, Tailored to Your Needs</p>
  <a class="abs btn frac-btn">AVAILABLE PROGRAMS</a>
  <div class="abs scroll-cue"><svg width="18" height="12" viewBox="0 0 18 12"><path d="M2 2l7 7 7-7" fill="none" stroke="#000" stroke-width="2.6" stroke-linecap="round"/></svg></div>

  <div class="abs benefit" style="left:219px">
    <svg width="34" height="34" viewBox="0 0 34 34"><circle cx="15" cy="18" r="12" fill="none" stroke="#fff" stroke-width="2"/><text x="15" y="23" text-anchor="middle" font-family="Montserrat" font-weight="700" font-size="14" fill="#fff">$</text><path d="M24 10l7-7M27 3h4v4" fill="none" stroke="#fff" stroke-width="2"/></svg>
    <p>Fractional ownership offers private jet benefits without full ownership costs, ideal for frequent flyers.</p>
    <div class="label">COST EFFECTIVE</div>
  </div>
  <div class="abs benefit" style="left:412px">
    <svg width="34" height="34" viewBox="0 0 34 34"><circle cx="17" cy="5" r="3.5" fill="#fff"/><path d="M6 11h22M17 11v10M17 21l-6 11M17 21l6 11" stroke="#fff" stroke-width="3" stroke-linecap="round"/></svg>
    <p>Gain reliable access to a fleet of private aircraft for convenient and luxur travel.</p>
    <div class="label">ACCESSIBILITY</div>
  </div>
  <div class="abs benefit" style="left:605px">
    <svg width="34" height="34" viewBox="0 0 34 34"><rect x="3" y="3" width="28" height="28" rx="3" fill="none" stroke="#fff" stroke-width="2"/><circle cx="17" cy="17" r="7" fill="none" stroke="#fff" stroke-width="2.4"/><circle cx="17" cy="17" r="2.5" fill="#fff"/></svg>
    <p>Fractional ownership provides access to a private jet fleet with the flexibility to schedule flights according to your needs.</p>
    <div class="label">FLEXIBILITY</div>
  </div>
  <div class="abs benefit" style="left:798px">
    <svg width="34" height="34" viewBox="0 0 34 34"><circle cx="20" cy="11" r="7" fill="none" stroke="#fff" stroke-width="2"/><path d="M17 11l2 2 4-4" fill="none" stroke="#fff" stroke-width="2"/><path d="M3 26l8-4h9l-2 4h-7M3 31l9-1 14-7" fill="none" stroke="#fff" stroke-width="2" stroke-linecap="round"/></svg>
    <p>Skip the hassles of commercial air travel with streamlined booking processes &amp; personalised service.</p>
    <div class="label">CONVENIENCE</div>
  </div>

  <!-- Re-defining aviation luxury -->
  <h2 class="abs redef-title">Re-Defining Aviation Luxury</h2>
  <p class="abs redef-tags">Jet Card | Private Jet Lease | All Access | Helicopter Access | By-the Seat Charter</p>
  <p class="abs redef-copy">Experience the epitome of luxury travel with Velorane's premium programs this includes from flexible Jet Card access to consistent ownership benefits with Private Jet Lease Programs, we cater to diverse travel needs. Unlock unlimited travel possibilities with All Access Programs, and enjoy seamless integration with Helicopter Access Programs. For solo travellers or small groups, By-the-Seat Charter Flights offer cost-effective luxury travel. Elevate every journey with Velorane's unparalleled service and convenience.</p>
  <a class="abs btn redef-btn">EXPLORE BENEFITS</a>
  <div class="abs redef-photo" role="img" aria-label="Black and white view of a passenger working on a laptop beside a cabin window"></div>

  <!-- Elevate your journey -->
  <div class="abs elevate-photo" role="img" aria-label="Aircraft wing above the clouds against a deep blue sky"></div>
  <h2 class="abs elevate-title">ELEVATE YOUR JOURNEY</h2>
  <p class="abs elevate-tags">Unparalleled Experience | Luxurious Comfort | Personalised Service</p>
  <p class="abs elevate-copy">Whether you're traveling for business or pleasure, Velorane is dedicated to provide with the highest level of service and comfort. Experience the difference with Velorane and elevate your travel experience to new heights.</p>

  <div class="abs service" style="left:388px">
    <svg width="24" height="24" viewBox="0 0 24 24"><rect x="2" y="4" width="20" height="18" rx="2" fill="#fff"/><circle cx="13" cy="14" r="5" fill="#1f5a96"/><path d="M13 11v3h2" stroke="#fff" stroke-width="1.5" fill="none"/></svg>
    ON-DEMAND<br>CHARTER
  </div>
  <div class="abs service" style="left:545px">
    <svg width="24" height="24" viewBox="0 0 24 24"><path d="M14 2h4v4h4v4h-4v4h-4v-4h-4V6h4z" fill="#fff"/><path d="M2 22v-6h5l4 3h6" fill="none" stroke="#fff" stroke-width="2"/></svg>
    GLOBAL MEDICAL<br>RESPONSE
  </div>
  <div class="abs service" style="left:701px">
    <svg width="24" height="24" viewBox="0 0 24 24"><circle cx="12" cy="12" r="10" fill="none" stroke="#fff" stroke-width="2"/><circle cx="12" cy="12" r="5" fill="none" stroke="#fff" stroke-width="2"/><circle cx="12" cy="12" r="1.6" fill="#fff"/></svg>
    PERSONALISED<br>SERVICES
  </div>
  <p class="abs elevate-cta">READY TO SOAR? CONTACT US TODAY FOR YOUR PERSONALISED CONSULTATION!</p>
  <a class="abs btn elevate-btn">BOOK CALL NOW</a>

  <!-- Testimonials -->
  <div class="abs testi-bg" role="img" aria-label="Dotted world map with faint flight paths"></div>
  <h2 class="abs testi-title">Explore Real Testimonials Highlighting the excellence of Velorane's Service, Ready to Experience Luxury Travel ? Book Your Journey Today!</h2>
  <a class="abs btn testi-btn">BOOK CALL NOW</a>

  <div class="bubble" style="left:631px;top:1956px;width:342px;height:206px">
    <svg width="342" height="206" viewBox="0 0 342 206"><path d="M14 20 Q16 8 30 8 L320 0 Q342 0 338 22 L316 150 Q312 166 296 166 L254 168 L244 200 L240 168 L28 180 Q10 180 10 162 Z" fill="#fff"/></svg>
    <p style="left:24px;top:90px;width:300px">Velorane sets the standard for luxury travel. Impeccable service from booking to landing &nbsp;- Maren K.</p>
    <div class="quote-mark" style="left:-10px;top:14px">“</div>
  </div>
  <div class="bubble" style="left:214px;top:2132px;width:342px;height:206px">
    <svg width="342" height="206" viewBox="0 0 342 206"><path d="M6 14 Q8 0 24 2 L324 18 Q340 20 340 38 L338 154 Q336 170 320 170 L92 170 L96 206 L72 172 L40 172 Q24 172 22 156 Z" fill="#fff"/></svg>
    <p style="left:42px;top:72px;width:280px">Velorane exceeded all my expectations! Impeccable service, luxurious amenities, and seamless travel experience. Highly recommend &nbsp;- Elias R.</p>
    <div class="quote-mark" style="left:300px;top:14px">”</div>
  </div>

  <!-- Partners & newsletter -->
  <span class="abs partner" style="left:218px">AERQUILL</span>
  <span class="abs partner" style="left:383px">SKYMARROW</span>
  <span class="abs partner" style="left:552px">FENDAIR</span>
  <span class="abs partner" style="left:698px">CORVAYNE</span>
  <span class="abs partner" style="left:850px">LUMAVANE</span>
  <p class="abs newsletter-text">Stay Updated with Exclusive Offers and Industry News<br>Subscribe to Our Newsletter</p>
  <div class="abs email-field">enter your email</div>
  <a class="abs btn subscribe-btn">SUBSCRIBE NOW</a>

  <!-- FAQ -->
  <div class="abs faq-photo" role="img" aria-label="White and red private jet parked in a dark hangar"></div>
  <h2 class="abs faq-title">FAQs: Your Questions Answered</h2>
  <p class="abs faq-item" style="top:2686px">What services does Velorane offer?</p>
  <div class="abs faq-rule" style="top:2711px"></div>
  <p class="abs faq-item" style="top:2729px">How does fractional jet ownership work?</p>
  <div class="abs faq-rule" style="top:2763px"></div>
  <p class="abs faq-item" style="top:2771px">What are the benefits of joining a jet card program with Velorane?</p>
  <div class="abs faq-rule" style="top:2815px"></div>
  <p class="abs faq-item" style="top:2836px">Can I customise my flight itinerary with Velorane?</p>
  <div class="abs faq-rule" style="top:2867px"></div>
  <p class="abs faq-item" style="top:2878px">What safety measures does Velorane have in place?</p>
  <p class="abs faq-answer">Velorane prioritises safety above all else. We adhere to rigorous safety standards and protocols, including thorough aircraft maintenance, regular inspections, and employing highly trained and experienced flight crews. Additionally, we monitor weather conditions and air traffic to ensure safe and efficient flight operations. Rest assured, your safety is our top priority at Velorane.</p>

  <!-- Footer -->
  <div class="abs brand footer-brand"><span>Velorane</span><span class="brand-mark"></span></div>
  <p class="abs footer-tag">Redefining Luxury Travel with Convenience, Opulence, and personalised Service, elevate Your Journey with us.</p>
  <span class="abs social" style="left:216px"></span>
  <span class="abs social" style="left:247px"></span>
  <span class="abs social" style="left:278px"></span>
  <nav class="abs footer-links">
    <span>Aircraft</span><span>Programs</span><span>Why velorane</span><span>Lifestyle</span><span>Sustainability</span><span>Resources</span><span>Competitors</span><span>Inquire</span>
  </nav>
  <div class="abs footer-rule"></div>

  <h3 class="abs contact-title">Contact us</h3>
  <div class="abs contact-row" style="top:3227px">
    <svg width="14" height="10" viewBox="0 0 14 10"><rect width="14" height="10" fill="#fff"/><path d="M0 0l7 6 7-6" fill="none" stroke="#000" stroke-width="1.2"/></svg>
    <span>info@velorane.com<br>mailto:info@velorane.com</span>
  </div>
  <div class="abs contact-row" style="top:3281px">
    <svg width="14" height="14" viewBox="0 0 14 14"><circle cx="7" cy="7" r="7" fill="#fff"/><path d="M4.5 3.5l1.5 1.5-1 1.2q1 2 3 3l1.2-1 1.5 1.5-1 1.3q-4-1-6.3-6.2z" fill="#000"/></svg>
    <span>800-555-0147</span>
  </div>
  <div class="abs contact-row" style="top:3318px">
    <svg width="14" height="16" viewBox="0 0 14 16"><path d="M7 16S1 9 1 6a6 6 0 0 1 12 0c0 3-6 10-6 10z" fill="#fff"/><circle cx="7" cy="6" r="2" fill="#000"/></svg>
    <span>2280 Harbor Crest Ave, Suite 4<br>Coral Vista, Florida 33010</span>
  </div>

  <p class="abs footer-cta">Ready to elevate your travel experience? Book your flight now or contact Velorane for more information and start your journey in luxury &amp; convenience today !</p>
  <a class="abs btn btn-white footer-btn">BOOK CALL NOW</a>

  <div class="abs legal-bar">
    <span style="left:214px">© 2024 Velorane, All rights reserved</span>
    <span style="left:810px">Terms of Use | Privacy Policy</span>
  </div>
</div>
</body>
</html>
```